B2B Case Study Template Design (InDesign or Affinity Designer)

Hello,We are a company specializing in custom sanitary space fit-outs and Solid Surface manufacturing. We are looking for a talented layout designer to create a professional and modern "Case Study" template to showcase our projects.This template must strictly be designed using Adobe InDesign or Affinity Designer. We do not want Canva, Word, or PowerPoint files.Attached, there is a file you can reference named "Brelo - Case Study.pdf". This is our previous layout.

Your mission is to recreate this case study using our new brand guidelines (which I will also provide) while using the exact same texts, photos, and sections (Key Data / "Données clés", Valkor's Role / "Le rôle d'Valkor", Valkor Products / "Produits Valkor").

Note: This project is the first of a series. We want to keep everything in the same project scope moving forward. If the work is satisfactory, we will hire you directly for upcoming print materials (flyer templates, catalogs, etc.).

---
2 Exemples of existing Case Studies : BRELO and TOLVEN
1 Full INDISIGN assembled file for MURESK project (you can work from there)
The logo (multi format)
And a zip file with the PATTERN, FONT and LOGO ALTERNATIVES (for graphic use only - on a photo, or else)

Target Market(s)

Building professionals, architects, specifiers, B2B companies, and contractors.

Industry/Entity Type

Architecture / Construction / B2B

Font styles to use
Sans Serif

Requirements
Must have
• The final source file must be delivered in Adobe InDesign (.indd/.idml) or Affinity Designer format. The design must be clean, structured, and highlight the architectural photography. Paragraph and character styles must be properly set up in the software so we can easily edit the text ourselves in the future. Strict integration of our new brand guidelines (colors, typography).
Nice to have
• A modular design: a layout that works perfectly for a 2-page (front/back) document, but can be easily expanded to 3 or 4 pages if a specific case study requires more content. Layout suggestions for recurring graphic elements (e.g., custom icons for key data, elegant frames for pull quotes).
Should not have
• Do NOT use Canva, Microsoft Word, or Photoshop for the layout. Avoid cluttered, overly colorful, or whimsical designs. We are looking for a premium, high-end, and serious aesthetic suited for the architectural field.

```html
<!DOCTYPE html>
<html lang="fr">
<head>
<meta charset="utf-8">
<title>Projet Muresk – Étude de cas</title>
<link rel="stylesheet" href="https://fonts.googleapis.com/css2?family=Poppins:wght@300;400;500;600;700;800&family=Archivo+Black&display=swap">
<style>
:root{
  --ink:#2b2a28;
  --paper:#e9e6e0;
  --page:#ffffff;
  --light:#f4f2ee;
  --muted:#cfcac2;
  --wall:#5e6b45;
  --wood:#9a6a3f;
  --sink:#f3f3f1;
}
*{margin:0;padding:0;box-sizing:border-box}
html,body{width:849px;height:1200px;overflow:hidden;background:var(--page)}
body{position:relative;font-family:"Poppins",sans-serif;color:var(--ink)}
.spread{position:absolute;left:43px;width:763px;height:271px;background:var(--ink)}
.s1{top:29px}.s2{top:321px}.s3{top:613px}.s4{top:905px}
.box{position:absolute}
.paper{background:var(--paper)}
.photo{position:absolute}
.photo-vanity{background:
  linear-gradient(180deg,var(--wall) 0%,#4d5838 30%,var(--sink) 31%,#ffffff 55%,var(--wood) 57%,#7d5230 100%)}
.photo-room{background:
  linear-gradient(180deg,#6c7552 0%,#3f4732 40%,#dcdcd8 62%,#c9c6c0 100%)}
.photo-corner{background:
  linear-gradient(160deg,var(--wall) 0%,#525d3d 40%,#e6e4e0 55%,#ffffff 70%,var(--wood) 72%,#7b5130 100%)}
.letter{position:absolute;font-weight:600;line-height:1;font-size:44px}
.on-dark{color:#fff}
.on-light{color:#000}
.title-heavy{font-family:"Archivo Black",sans-serif;letter-spacing:.2px}
.upper{text-transform:uppercase}
/* spread 1 */
.contact{position:absolute;left:51px;top:120px;width:70px;font-size:4.6px;line-height:1.45}
.contact .rule{width:12px;height:.6px;background:#000;margin-bottom:9px}
.contact h3{font-size:6.6px;font-weight:600;margin-bottom:7px}
.contact h4{font-size:4.6px;font-weight:600;margin:0 0 3px}
.contact p{margin-bottom:8px}
.cover-title{position:absolute;left:589px;top:192px;color:#fff}
.cover-title h1{font-size:14.5px;line-height:1}
.cover-title p{font-size:9.6px;font-weight:300;line-height:1.33;margin-top:6px;letter-spacing:.3px}
/* spread 2 */
.facts{position:absolute;left:414px;top:27px;width:122px;color:#fff;font-size:4.4px;line-height:1.4}
.facts h2{font-size:8.6px}
.facts .lede{font-size:7.3px;font-weight:300;line-height:1.15;margin-bottom:7px}
.facts h3{font-size:7px;font-weight:300;margin:4px 0 3px}
.facts ul{list-style:none;margin-bottom:4px}
.facts li{position:relative;padding-left:4px;margin-bottom:2.6px;font-weight:300}
.facts li::before{content:"•";position:absolute;left:0}
.facts li b{font-weight:600}
.facts .para{font-weight:300;margin-bottom:6px;text-align:justify}
.facts .para b{font-weight:600}
.products{display:flex;gap:14px;margin-top:3px}
.product{width:30px;height:30px;border-radius:50%;background:radial-gradient(circle at 40% 35%,#ffffff,#bdbab4)}
/* spread 3 */
.wordmark{position:absolute;left:54px;top:78px;font-size:27px;font-weight:600;letter-spacing:5px;color:#000;line-height:1}
.challenge{position:absolute;left:54px;top:112px;width:230px;font-size:4.5px;line-height:1.45}
.challenge h2{font-size:8.8px;font-weight:400;margin-bottom:5px}
.challenge h3{font-size:5.8px;font-weight:400;margin-bottom:6px}
.challenge .lead{font-weight:700;margin-bottom:3px}
.challenge p{font-weight:300}
.cols{display:flex;gap:12px;margin-top:9px}
.col{width:109px}
.col h4{font-size:6.5px;font-weight:400;margin-bottom:7px}
.col p{margin-bottom:6px}
/* spread 4 */
.furniture{position:absolute;left:204px;top:36px;width:88px;font-size:4.5px;line-height:1.45}
.furniture h2{font-size:9px;line-height:1.1}
.furniture .sub{font-size:8.6px;font-weight:400;line-height:1.15;margin-bottom:10px}
.furniture h3{font-size:6px;font-weight:400;line-height:1.3;margin-bottom:14px}
.furniture .lead{font-weight:700}
.furniture p{font-weight:300;text-align:justify;margin-bottom:6px}
.drawing{position:absolute;left:303px;top:34px;width:58px;height:217px;background:linear-gradient(180deg,#ededeb,#d9d5cf)}
.process{position:absolute;left:400px;top:36px;width:163px;font-size:4.4px;line-height:1.45}
.process h2{font-size:9px;line-height:1.1}
.process .sub{font-size:8.4px;margin-bottom:8px}
.process h3{font-size:6px;font-weight:400;line-height:1.25;margin-bottom:8px}
.process .lead{font-weight:700;margin-bottom:6px}
.process ul{list-style:none}
.process li{position:relative;padding-left:5px;margin-bottom:6px;font-weight:300}
.process li::before{content:"•";position:absolute;left:0}
.process li b{font-weight:700;display:block}
.process .twocol{column-count:2;column-gap:9px;font-weight:300;text-align:justify}
.process .twocol p{margin-bottom:5px}
.caption{position:absolute;left:578px;top:35px;font-size:4.4px;font-weight:300}
.site-photo{position:absolute;left:578px;top:43px;width:158px;height:98px;background:linear-gradient(180deg,#6d7656 0%,#56603f 55%,#ece9e6 56%,#d8d3cf 100%)}
.pattern{position:absolute;left:578px;top:146px;width:158px;height:100px;background:repeating-linear-gradient(135deg,#d9d5ce 0 2px,var(--paper) 2px 7px)}
</style>
</head>
<body>

<!-- Spread 1: cover -->
<section class="spread s1">
  <div class="box paper" style="left:6px;top:6px;width:375px;height:259px"></div>
  <span class="letter on-light" style="left:50px;top:63px">N</span>
  <span class="letter on-light" style="left:122px;top:63px">E</span>
  <span class="letter on-light" style="left:122px;top:128px">V</span>
  <span class="letter on-light" style="left:122px;top:193px">R</span>
  <span class="letter on-light" style="left:186px;top:193px">A</span>
  <div class="contact">
    <div class="rule"></div>
    <h3>Prendre contact.</h3>
    <h4>Adresse</h4>
    <p>Les Combes,<br>43210 Montrevel<br>France.</p>
    <h4>Site Web</h4>
    <p>www.valkor.fr<br>info@valkor.fr</p>
    <h4>Téléphone</h4>
    <p>+33 4 71 55 20 34</p>
  </div>
  <div class="photo photo-vanity" style="left:382px;top:6px;width:178px;height:259px" role="img" aria-label="Photo d'un plan vasque blanc sur meuble bois, mur vert et miroir"></div>
  <span class="letter on-dark" style="left:586px;top:24px">N</span>
  <span class="letter on-dark" style="left:586px;top:83px">E</span>
  <span class="letter on-dark" style="left:586px;top:141px">V</span>
  <span class="letter on-dark" style="left:650px;top:141px">R</span>
  <span class="letter on-dark" style="left:710px;top:141px">A</span>
  <div class="cover-title">
    <h1 class="title-heavy upper">Projet Muresk</h1>
    <p class="upper">L'art de l'agilité:<br>Rénovation sanitaire<br>en site occupé</p>
  </div>
</section>

<!-- Spread 2: key data -->
<section class="spread s2">
  <div class="photo photo-room" style="left:6px;top:6px;width:376px;height:259px" role="img" aria-label="Photo d'un sanitaire avec double vasque, miroir et sèche-mains"></div>
  <div class="facts">
    <h2 class="title-heavy upper">Projet Muresk:</h2>
    <p class="lede">quand la performance s'adapte à la continuité de service</p>
    <h3 class="upper">Données clé</h3>
    <ul>
      <li><b>Lieu:</b> 12 Rue Ferrand, Paris 17e (immeuble bureaux Premium)</li>
      <li><b>Maître d'ouvrage:</b> Halvern Banque</li>
      <li><b>Maître d'œuvre:</b> Orvel</li>
      <li><b>Livraison:</b> 2026</li>
    </ul>
    <h3 class="upper">Le rôle d'Valkor</h3>
    <ul>
      <li>Conception de mobilier SORVANE sur-mesure à profondeur variable</li>
      <li>Planification de pose par tranches</li>
      <li>Logistique de propreté «Zéro Poussière»</li>
      <li>Installation en mode «Discret»</li>
    </ul>
    <p class="para"><b>L'enjeu majeur du chantier Muresk résidait dans:</b> l'environnement immédiat: des open spaces occupés par des collaborateurs en plein travail.</p>
    <p class="para">Ce projet exigeait donc une discrétion absolue et une rapidité d'exécution chirurgicale, dans le but de maintenir le confort des usagers pendant la transformation des espaces sanitaires.</p>
    <h3 class="upper">Produits Valkor</h3>
    <div class="products">
      <div class="product" role="img" aria-label="Vignette produit: plan vasque"></div>
      <div class="product" role="img" aria-label="Vignette produit: vasque Solid Surface"></div>
      <div class="product" role="img" aria-label="Vignette produit: habillage mural"></div>
    </div>
  </div>
  <div class="box paper" style="left:564px;top:6px;width:193px;height:259px"></div>
  <span class="letter on-light" style="left:581px;top:23px">N</span>
  <span class="letter on-light" style="left:645px;top:23px">E</span>
  <span class="letter on-light" style="left:710px;top:23px">V</span>
  <span class="letter on-light" style="left:645px;top:86px">R</span>
  <span class="letter on-light" style="left:710px;top:148px">A</span>
</section>

<!-- Spread 3: the challenge -->
<section class="spread s3">
  <div class="box paper" style="left:6px;top:6px;width:374px;height:259px"></div>
  <div class="wordmark">NEVRA</div>
  <div class="challenge">
    <h2 class="upper">Une prouesse d'agilité: le défi du site occupé</h2>
    <h3 class="upper">Maintenir le confort des usagers pendant la mutation des espaces.</h3>
    <p class="lead">L'enjeu majeur du chantier Muresk résidait dans l'environnement immédiat:</p>
    <p>des open spaces occupés par des collaborateurs en plein travail.<br>Ce projet « Muresk » exigeait donc une discrétion absolue et une rapidité d'exécution chirurgicale.</p>
    <div class="cols">
      <div class="col">
        <h4 class="upper">1. Mode «Discret» &amp; propreté:</h4>
        <p>Travailler dans le silence et sans dégagement de poussière était une condition non négociable.</p>
        <p>Valkor a mis en place un protocole spécifique pour garantir une propreté absolue des parties communes et des sanitaires, permettant aux occupants de continuer leurs activités sans nuisance.</p>
      </div>
      <div class="col">
        <h4 class="upper">2. Flux de travail «Chrono»</h4>
        <p>Pour éviter la fermeture simultanée de tous les sanitaires de l'immeuble, Valkor a orchestré une pose par tranches successives.</p>
        <p>Ce phasage dynamique a permis de maintenir la continuité de service pour le client tout en assurant un temps de travaux record par étage.</p>
      </div>
    </div>
  </div>
  <div class="photo photo-vanity" style="left:380px;top:6px;width:377px;height:259px" role="img" aria-label="Photo d'un double plan vasque blanc dans un sanitaire aux murs verts"></div>
</section>

<!-- Spread 4: furniture and process -->
<section class="spread s4">
  <div class="box paper" style="left:6px;top:6px;width:751px;height:259px"></div>
  <div class="photo photo-corner" style="left:6px;top:6px;width:171px;height:259px" role="img" aria-label="Photo d'une vasque dans une niche avec sèche-mains"></div>
  <div class="furniture">
    <h2 class="title-heavy upper">Mobilier Sorvane:</h2>
    <p class="sub upper">L'intelligence du sur-mesure</p>
    <h3 class="upper">S'adapter à l'existant sans compromis sur le design.</h3>
    <h3 class="upper">Le projet Muresk a nécessité une adaptation rare de notre gamme de supports de fixation.</h3>
    <p class="lead">Profondeurs atypiques:</p>
    <p>Le bureau d'études Valkor a redessiné le mobilier SORVANOL pour répondre à des profondeurs de niches sortant des standards habituels, optimisant ainsi chaque centimètre carré d'espace.</p>
    <p>De plus, la redéfinition du support a permis l'ajout de rangements sous-jacents, permettant le stockage de matériel d'entretien, etc.</p>
  </div>
  <div class="drawing" role="img" aria-label="Plan coté et vue 3D du meuble vasque en niche"></div>
  <div class="process">
    <h2 class="title-heavy upper">De la conception à la pose:</h2>
    <p class="sub upper">La maîtrise de A à Z</p>
    <h3 class="upper">Une responsabilité totale pour<br>un résultat garanti.</h3>
    <p class="lead">Au-delà de la technique, ce projet représente également comment la société Valkor prend la responsabilité du résultat final en assurant elle-même la pose de ses produits.</p>
    <ul>
      <li><b>Manutention maîtrisée: Une logistique invisible en milieu occupé</b>Livraison et acheminement en milieu occupé sans perturber les flux de l'immeuble, en dehors des pics d'affluence.</li>
      <li><b>Précision de pose: L'ingénierie face aux contraintes de la rénovation</b>Ajustement des structures sur-mesure sur des supports existants parfois irréguliers &amp; redimensionnement du mobilier Sorvane pour s'adapter aux contraintes présentes et modification de sa profondeur.</li>
      <li><b>Engagement rapidité: un phasage précis pour la continuité de service</b></li>
    </ul>
    <div class="twocol">
      <p>L'installation a été orchestrée par tranches successives pour éviter la fermeture simultanée de tous les points d'eau et maintenir le confort des collaborateurs.</p>
      <p>Grâce à un pré-montage maximal dans notre atelier de Haute-Loire, le temps d'intervention physique sur le site de Muresk a été réduit au strict minimum.</p>
      <p>Chaque journée s'est conclue par un nettoyage rigoureux «fin de poste», permettant une restitution immédiate des locaux, sans poussière ni nuisances.</p>
    </div>
  </div>
  <div class="caption">RS - Muresk 1 - Femmes</div>
  <div class="site-photo" role="img" aria-label="Photo de relevé sur site avec cotes du mur sanitaire"></div>
  <div class="pattern" role="img" aria-label="Motif répété de la marque"></div>
</section>

</body>
</html>
```